SaaS Early tech startup business card design

Unique design for experience ecommerce platform company. the business cards will be used by executive members. conformance with color code is required.

```html
<!DOCTYPE html>
<html lang="en">
<head>
<meta charset="utf-8">
<title>Velto Business Card</title>
<link href="https://fonts.googleapis.com/css2?family=Arimo:wght@400;700&display=swap" rel="stylesheet">
<style>
  :root {
    --brand-blue: #18658f;
    --brand-teal: #1aa88d;
    --card-white: #ffffff;
    --backdrop: #cfcfcf;
    --text-light: #ffffff;
  }
  * { margin: 0; padding: 0; box-sizing: border-box; }
  html, body { width: 1200px; height: 788px; overflow: hidden; }
  body {
    background: var(--backdrop);
    font-family: "Arimo", Arial, sans-serif;
    position: relative;
  }
  .card {
    position: absolute;
    top: 245px;
    width: 520px;
    height: 297px;
    border-radius: 22px;
    overflow: hidden;
    box-shadow: 0 10px 24px rgba(0,0,0,0.25);
  }
  .card-front { left: 60px; background: var(--card-white); }
  .card-back { left: 620px; background: var(--brand-blue); }

  .wave { position: absolute; inset: 0; width: 520px; height: 297px; }
  .wave-fill { fill: var(--brand-blue); }
  .wave-accent { fill: none; stroke: var(--brand-teal); stroke-width: 3; }

  .brand-name {
    position: absolute;
    font-weight: 700;
    letter-spacing: -1px;
    line-height: 1;
  }
  .card-front .brand-name {
    left: 262px; top: 14px;
    font-size: 54px;
    color: var(--brand-teal);
  }
  .card-back .brand-name {
    left: 0; right: 0; top: 98px;
    text-align: center;
    font-size: 104px;
    color: var(--card-white);
  }

  .contact-block {
    position: absolute;
    left: 34px;
    top: 162px;
    color: var(--text-light);
  }
  .person-name {
    color: var(--brand-teal);
    font-weight: 700;
    font-size: 15px;
    letter-spacing: 1px;
    line-height: 18px;
  }
  .person-title { font-size: 11px; line-height: 14px; margin: 1px 0 6px; }
  .contact-list { list-style: none; font-size: 10.5px; line-height: 14px; }
  .contact-list li { display: flex; align-items: center; gap: 6px; }
  .contact-icon { width: 9px; height: 9px; fill: var(--brand-teal); flex: none; }

  .address {
    position: absolute;
    right: 22px;
    top: 132px;
    text-align: right;
    color: var(--text-light);
    font-size: 10.5px;
    font-style: normal;
    line-height: 14px;
  }
</style>
</head>
<body>
  <section class="card card-front">
    <svg class="wave" viewBox="0 0 520 297" aria-hidden="true">
      <path class="wave-fill" d="M0,297 L0,178 C18,142 80,132 200,117 C330,100 455,82 505,0 L520,0 L520,297 Z"/>
      <path class="wave-accent" d="M0,164 C20,130 80,120 200,105 C330,88 450,70 493,0"/>
    </svg>
    <div class="brand-name">velto</div>

    <div class="contact-block">
      <p class="person-name">DANA MERCER</p>
      <p class="person-title">Owner/CEO</p>
      <ul class="contact-list">
        <li><svg class="contact-icon" viewBox="0 0 10 10"><path d="M2 0.5 L3.8 2.8 L2.8 3.8 C3.5 5.2 4.8 6.5 6.2 7.2 L7.2 6.2 L9.5 8 L8.2 9.5 C4.2 9.2 0.8 5.8 0.5 1.8 Z"/></svg>(555) 210 - 48372</li>
        <li><svg class="contact-icon" viewBox="0 0 10 10"><rect x="1" y="3" width="8" height="6" rx="1"/><rect x="0" y="1" width="10" height="2" rx="1"/></svg>(555) 377 - 60914</li>
        <li><svg class="contact-icon" viewBox="0 0 10 10"><path d="M0 2 H10 V8 H0 Z M0 2 L5 5.5 L10 2" stroke="#18658f" stroke-width="0.8"/></svg>dana@veltogroup.com</li>
        <li><svg class="contact-icon" viewBox="0 0 10 10"><circle cx="5" cy="5" r="4.5"/></svg>www.veltogroup.com</li>
      </ul>
    </div>

    <address class="address">210 - 4480 18 Ave<br>Lakeview, BC V2K1M7</address>
  </section>

  <section class="card card-back">
    <div class="brand-name">velto</div>
  </section>
</body>
</html>
```